Verodex business card

Business card for sustainable investment company called "Verodex". Verodex is an exchange platform selling carbon credits between buyers and sellers. Carbon Credits are an environmental commodity for reducing global carbon emissions.

the card should obviously have our logo and the theme should be sustainability/environment mixed with a trading platform.

Contact Information for Business Card

Logo, Name, Title, Phone, Email

Colors
0054AA
0677BA
7BADD7
CADEEF
E8F1F8
0094D4
00A9DD
6FCCEA
C7EBF8
E9F6FB
00AB8E
00BBA5
67D7C9
C6EFE9
E9F9F6
59FF00
82FF00
B8FF75
E3FFCB
F4FFEA

```html
<!DOCTYPE html>
<html lang="en">
<head>
<meta charset="utf-8">
<title>Verodex business card</title>
<link rel="stylesheet" href="https://fonts.googleapis.com/css2?family=Montserrat:wght@600;700&family=Arimo:wght@400&display=swap">
<style>
  :root{
    --stage:#1f1f1f;
    --card-dark:#161616;
    --card-light:#ffffff;
    --ink:#1a2b45;
    --ink-soft:#111111;
    --accent:#1a7fe6;
    --accent-bright:#00a9dd;
    --emboss:#2c2c2c;
  }
  *{margin:0;padding:0;box-sizing:border-box}
  html,body{width:1200px;height:1040px;overflow:hidden;background:var(--stage)}
  .stage{position:relative;width:1200px;height:1040px}
  .card{
    position:absolute;left:220px;width:760px;height:434px;
    border-radius:0 72px 0 72px;
  }
  .card--back{top:70px;background:var(--card-dark)}
  .card--front{top:536px;background:var(--card-light)}

  .brand{
    position:absolute;display:flex;align-items:center;gap:18px;
    font-family:"Montserrat",sans-serif;font-weight:700;letter-spacing:.02em;
  }
  .brand__mark{border-radius:50%}
  .card--back .brand{left:50%;top:50%;transform:translate(-50%,-50%)}
  .card--back .brand__mark{width:74px;height:74px;background:var(--emboss)}
  .card--back .brand__name{font-size:68px;color:var(--emboss)}

  .card--front .brand{left:58px;top:185px;gap:12px}
  .card--front .brand__mark{width:42px;height:42px;background:var(--accent-bright)}
  .card--front .brand__name{font-size:40px;color:var(--ink)}

  .divider{position:absolute;left:372px;top:112px;width:1px;height:210px;background:var(--accent)}

  .contact{position:absolute;left:400px;top:138px}
  .contact__name{font-family:"Montserrat",sans-serif;font-weight:700;font-size:25px;color:var(--ink);letter-spacing:.03em}
  .contact__title{font-family:"Arimo",sans-serif;font-size:19px;color:var(--ink-soft);margin-top:2px;letter-spacing:.03em}
  .contact__list{list-style:none;margin-top:18px}
  .contact__item{display:flex;align-items:center;gap:10px;font-family:"Arimo",sans-serif;font-size:20px;color:var(--ink-soft);letter-spacing:.04em;line-height:30px}
  .contact__icon{width:20px;height:20px;flex:none}
  .contact__highlight{color:var(--accent)}
</style>
</head>
<body>
<main class="stage">
  <section class="card card--back" aria-label="Card back">
    <div class="brand">
      <span class="brand__mark"></span>
      <span class="brand__name">VERODEX</span>
    </div>
  </section>

  <section class="card card--front" aria-label="Card front">
    <div class="brand">
      <span class="brand__mark"></span>
      <span class="brand__name">VERODEX</span>
    </div>
    <div class="divider"></div>
    <div class="contact">
      <p class="contact__name">MARCUS ELLERY</p>
      <p class="contact__title">Managing Director</p>
      <ul class="contact__list">
        <li class="contact__item">
          <svg class="contact__icon" viewBox="0 0 24 24" fill="none" stroke="#1a7fe6" stroke-width="2"><path d="M5 3h4l2 5-2.5 1.5a11 11 0 0 0 6 6L16 13l5 2v4a2 2 0 0 1-2 2A16 16 0 0 1 3 5a2 2 0 0 1 2-2z"/></svg>
          021-555 0184
        </li>
        <li class="contact__item">
          <svg class="contact__icon" viewBox="0 0 24 24" fill="#1a7fe6"><path d="M2 5h20v14H2z"/><path d="M2 5l10 8 10-8" fill="none" stroke="#fff" stroke-width="1.6"/></svg>
          hello@verodex.co
        </li>
        <li class="contact__item">
          <svg class="contact__icon" viewBox="0 0 24 24" fill="none" stroke="#1a7fe6" stroke-width="1.8"><circle cx="12" cy="12" r="10"/><ellipse cx="12" cy="12" rx="4.5" ry="10"/><path d="M2 12h20M4 7h16M4 17h16"/></svg>
          <span>www.<span class="contact__highlight">verodex</span>.co</span>
        </li>
      </ul>
    </div>
  </section>
</main>
</body>
</html>
```